Fernhollow Architectural Systems Business Card

We have a logo - but we need a business card. We are a specialty manufacturer of wood wall and ceiling panels. Please visit our website - www.fernhollowpanels.com to see examples of our products.
We create wood architectural systems - so we would love to see wood on the card somehow. Maybe something similar to our grille system?
We would like a spot on the business card for a QR code that people can scan to add the contact to their phone (we have the QR codes - just need a spot on the card).
As for the contact info - we want to keep it simple. (Name, Cell phone, Fax, email, website)

Target Market(s)

Architects and general contractors

Industry/Entity Type

Construction

Contact Information for Business Card

Name, Cell phone, fax, email, website

Requirements
Must have
• space for a QR code, wood feature
Nice to have
• We just want something a little different - but not too crazy. We want to stand out - but in a professional way.
Should not have
• nothing too busy

```html
<!DOCTYPE html>
<html lang="en">
<head>
<meta charset="utf-8">
<title>Fernhollow Architectural Systems – Business Card</title>
<link rel="stylesheet" href="https://fonts.googleapis.com/css2?family=Montserrat:wght@400;500;800&display=swap">
<style>
  :root {
    --stage: #e4e4e6;
    --card-white: #ffffff;
    --card-black: #141414;
    --pattern-dark: #1f1f1f;
    --pattern-light: #3a3a3a;
    --brand-red: #b3191f;
    --ink: #1a1a1a;
    --wood-light: #c08a55;
    --wood-mid: #9a6535;
    --wood-dark: #6e4220;
  }
  * { box-sizing: border-box; margin: 0; padding: 0; }
  html, body { width: 1200px; height: 912px; overflow: hidden; }
  body {
    background: var(--stage);
    font-family: "Montserrat", sans-serif;
    display: flex;
    flex-direction: column;
    align-items: center;
    justify-content: center;
    gap: 56px;
  }
  .card {
    position: relative;
    width: 640px;
    height: 366px;
    box-shadow: 0 10px 28px rgba(0,0,0,.22);
    overflow: hidden;
  }
  /* back */
  .card-back { background: var(--card-black); }
  .back-texture {
    position: absolute; inset: 0;
    background: linear-gradient(200deg, var(--pattern-light) 0%, var(--pattern-dark) 55%, var(--card-black) 100%);
  }
  .wood-feature {
    position: absolute; left: 0; top: 0; bottom: 0; width: 200px;
    background: linear-gradient(160deg, var(--wood-light) 0%, var(--wood-mid) 55%, var(--wood-dark) 100%);
  }
  .back-brand {
    position: absolute; right: 44px; top: 118px;
    display: flex; align-items: center; gap: 10px;
    color: var(--brand-red); font-weight: 800; font-size: 15px; letter-spacing: 1.5px;
  }
  .back-brand .dot { width: 14px; height: 14px; background: var(--brand-red); border-radius: 50%; }
  .qr-spot {
    position: absolute; right: 44px; bottom: 44px;
    width: 104px; height: 104px;
    background: var(--card-white);
    border-radius: 6px;
  }
  /* front */
  .card-front { background: var(--card-white); }
  .front-brand {
    position: absolute; left: 0; right: 0; top: 44px;
    text-align: center; color: var(--brand-red);
    font-weight: 800; font-size: 30px; letter-spacing: 2px; line-height: 1.05;
  }
  .front-brand small { display: block; font-size: 15px; letter-spacing: 4px; margin-top: 6px; }
  .person {
    position: absolute; left: 0; right: 0; top: 132px;
    display: flex; flex-direction: column; align-items: center;
  }
  .person-name-row { display: flex; align-items: center; gap: 14px; }
  .rule { width: 80px; height: 2px; background: var(--brand-red); }
  .person-name { color: var(--brand-red); font-weight: 800; font-size: 27px; letter-spacing: 2px; }
  .person-role { color: var(--ink); font-size: 15px; margin-top: 2px; }
  .divider { width: 380px; height: 1px; margin-top: 12px; background: linear-gradient(90deg, transparent, var(--brand-red), transparent); }
  .contacts {
    position: absolute; left: 0; right: 0; top: 214px;
    display: flex; flex-direction: column; align-items: center; gap: 4px;
    color: var(--ink); font-size: 14px;
  }
  .contact-row { display: flex; gap: 18px; }
  .contact { display: flex; align-items: center; gap: 6px; }
  .contact svg { width: 13px; height: 13px; fill: none; stroke: var(--brand-red); stroke-width: 2; }
  .band-red { position: absolute; left: 322px; right: 0; top: 290px; height: 30px; background: var(--brand-red); }
  .band-black { position: absolute; left: 0; width: 294px; top: 320px; height: 30px; background: var(--ink); }
  .band-dot {
    position: absolute; left: 290px; top: 300px; width: 36px; height: 36px;
    border-radius: 50%; background: var(--brand-red); border: 3px solid var(--card-white);
  }
</style>
</head>
<body>
  <section class="card card-back">
    <div class="back-texture" role="img" aria-label="Repeating tonal brand pattern in glossy black"></div>
    <div class="wood-feature" role="img" aria-label="Wood grille panel feature in warm oak tones"></div>
    <div class="back-brand"><span class="dot"></span>FERNHOLLOW</div>
    <div class="qr-spot" role="img" aria-label="Reserved space for contact QR code"></div>
  </section>

  <section class="card card-front">
    <div class="front-brand">FERNHOLLOW<small>ARCHITECTURAL SYSTEMS</small></div>

    <div class="person">
      <div class="person-name-row"><span class="rule"></span><span class="person-name">MARLOW KEATING</span><span class="rule"></span></div>
      <div class="person-role">Director</div>
      <div class="divider"></div>
    </div>

    <div class="contacts">
      <div class="contact-row">
        <span class="contact"><svg viewBox="0 0 14 14"><rect x="3.5" y="1" width="7" height="12" rx="1.5"/></svg>555-214-0387</span>
        <span class="contact"><svg viewBox="0 0 14 14"><rect x="2" y="6" width="10" height="6"/><rect x="4" y="2" width="6" height="4"/></svg>555-214-0388</span>
      </div>
      <div class="contact-row">
        <span class="contact"><svg viewBox="0 0 14 14"><rect x="1.5" y="3" width="11" height="8"/><path d="M1.5 3l5.5 4.5L12.5 3"/></svg>sales@fernhollowpanels.com</span>
        <span class="contact"><svg viewBox="0 0 14 14"><circle cx="7" cy="7" r="5.5"/><path d="M1.5 7h11M7 1.5c-3 3.5-3 7.5 0 11M7 1.5c3 3.5 3 7.5 0 11"/></svg>www.fernhollowpanels.com</span>
      </div>
      <div class="contact-row"><span class="contact">2207 Birchline Ave, Cedar Falls, IA 50613</span></div>
    </div>

    <div class="band-red"></div>
    <div class="band-black"></div>
    <div class="band-dot"></div>
  </section>
</body>
</html>
```